Veldmark Supplies Business Card

Professional business card that stand out to our potential customers. Front and back with clean modern design

Industry/Entity Type

Oil and gas

Contact Information for Business Card

Name, address, website , office phone and cell number

Requirements
Must have
• Editable files for each employee

```html
<!DOCTYPE html>
<html lang="en">
<head>
<meta charset="utf-8">
<title>Veldmark Supplies Business Card</title>
<link href="https://fonts.googleapis.com/css2?family=Montserrat:wght@400;500;700;800&display=swap" rel="stylesheet">
<style>
  :root {
    --stage: #2b2b2d;
    --card: #161616;
    --red: #e81f26;
    --blue: #17a7d3;
    --white: #f2f2f2;
    --muted: #d8d8d8;
  }
  * { margin: 0; padding: 0; box-sizing: border-box; }
  html, body {
    width: 1200px; height: 689px; overflow: hidden;
    background: var(--stage);
    font-family: "Montserrat", Arial, sans-serif;
  }
  .canvas {
    position: relative; width: 1200px; height: 689px;
    display: flex; align-items: center; justify-content: center; gap: 40px;
  }
  .card {
    position: relative; width: 540px; height: 309px;
    border-radius: 20px; background: var(--card);
    overflow: hidden;
    box-shadow: 0 18px 40px rgba(0,0,0,.45);
  }

  /* Back side */
  .card-back .pattern-field {
    position: absolute; inset: 0;
    background: linear-gradient(120deg, #cfcfcf 0%, #8d8d8d 22%, #3a3a3a 45%, #141414 62%, #0e0e0e 100%);
  }
  .card-back .brand-tag {
    position: absolute; left: 50%; top: 50%; transform: translate(-50%, -50%);
    display: flex; align-items: center; gap: 8px;
    background: var(--card); padding: 8px 14px; border-radius: 4px;
  }

  /* Brand lockup */
  .brand-square { width: 12px; height: 12px; background: var(--blue); flex: none; }
  .brand-name {
    font-weight: 800; color: var(--red);
    letter-spacing: .04em; text-transform: uppercase; white-space: nowrap;
  }
  .card-back .brand-name { font-size: 13px; }

  /* Front side */
  .card-front .brand-lockup {
    position: absolute; left: 30px; width: 250px; top: 50%; transform: translateY(-50%);
    display: flex; align-items: center; justify-content: center; gap: 9px;
  }
  .card-front .brand-square { width: 14px; height: 14px; }
  .card-front .brand-name { font-size: 16px; }

  .divider {
    position: absolute; left: 300px; top: 46px; bottom: 46px;
    width: 1.5px; background: var(--red);
  }
  .contact {
    position: absolute; left: 320px; top: 50px; right: 16px;
    color: var(--white);
  }
  .person-name {
    font-size: 22px; font-weight: 700; letter-spacing: .02em;
    text-transform: uppercase; line-height: 1; white-space: nowrap;
  }
  .person-name .first { color: var(--red); }
  .person-name .last { color: var(--blue); }
  .person-role { font-size: 12px; margin-top: 6px; color: var(--muted); }
  .address { font-size: 12px; line-height: 1.6; margin-top: 16px; }
  .details { list-style: none; margin-top: 14px; }
  .details li {
    display: flex; align-items: center; gap: 8px;
    font-size: 11.5px; line-height: 1.75; white-space: nowrap;
  }
  .details svg { width: 11px; height: 11px; flex: none; fill: var(--red); }
</style>
</head>
<body>
<main class="canvas">

  <section class="card card-back" aria-label="Card back">
    <div class="pattern-field" role="img" aria-label="Repeating brand-mark pattern fading from silver to black"></div>
    <div class="brand-tag">
      <span class="brand-square"></span>
      <span class="brand-name">Veldmark Supplies</span>
    </div>
  </section>

  <section class="card card-front" aria-label="Card front">
    <div class="brand-lockup">
      <span class="brand-square"></span>
      <span class="brand-name">Veldmark Supplies</span>
    </div>

    <div class="divider"></div>

    <div class="contact">
      <h1 class="person-name"><span class="first">Daniel</span> <span class="last">Carver</span></h1>
      <p class="person-role">Managing Director</p>
      <p class="address">418 N.Harlow Suite 5<br>Corbin, Tx 79842</p>
      <ul class="details">
        <li>
          <svg viewBox="0 0 24 24" aria-hidden="true"><path d="M6.6 10.8a15 15 0 0 0 6.6 6.6l2.2-2.2a1 1 0 0 1 1-.25 11.4 11.4 0 0 0 3.6.57 1 1 0 0 1 1 1V20a1 1 0 0 1-1 1A17 17 0 0 1 3 4a1 1 0 0 1 1-1h3.5a1 1 0 0 1 1 1c0 1.25.2 2.46.57 3.58a1 1 0 0 1-.25 1z"/></svg>
          (555)210-0471
        </li>
        <li>
          <svg viewBox="0 0 24 24" aria-hidden="true"><path d="M7 1h10a2 2 0 0 1 2 2v18a2 2 0 0 1-2 2H7a2 2 0 0 1-2-2V3a2 2 0 0 1 2-2zm0 3v14h10V4zm5 15.5a1 1 0 1 0 0 2 1 1 0 0 0 0-2z"/></svg>
          555 318 204
        </li>
        <li>
          <svg viewBox="0 0 24 24" aria-hidden="true"><path d="M2 5h20v14H2zm2 2v.5l8 5 8-5V7zm0 2.8V17h16V9.8l-8 5z"/></svg>
          sales@veldmarksupplies.com
        </li>
        <li>
          <svg viewBox="0 0 24 24" aria-hidden="true"><path d="M12 2a10 10 0 1 0 0 20 10 10 0 0 0 0-20zm6.9 6h-3a15.6 15.6 0 0 0-1.3-3.9A8 8 0 0 1 18.9 8zM12 4a14 14 0 0 1 1.9 4h-3.8A14 14 0 0 1 12 4zM4.3 14a8 8 0 0 1 0-4h3.4a16 16 0 0 0 0 4zm.8 2h3a15.6 15.6 0 0 0 1.3 3.9A8 8 0 0 1 5.1 16zm3-8h-3a8 8 0 0 1 4.3-3.9A15.6 15.6 0 0 0 8.1 8zM12 20a14 14 0 0 1-1.9-4h3.8A14 14 0 0 1 12 20zm2.3-6H9.7a14 14 0 0 1 0-4h4.6a14 14 0 0 1 0 4zm.3 5.9a15.6 15.6 0 0 0 1.3-3.9h3a8 8 0 0 1-4.3 3.9zm1.7-5.9a16 16 0 0 0 0-4h3.4a8 8 0 0 1 0 4z"/></svg>
          www.veldmarksupplies.com
        </li>
      </ul>
    </div>
  </section>

</main>
</body>
</html>
```